Logo + Label Design (Men’s Grooming Brand & Product Packaging)

Design a logo and 2 oz pomade label for Brel, a modern men’s grooming brand focused on clean, high-quality, natural ingredients. The design should establish a bold, masculine, minimalist identity that can later extend to products like shaving gel and body wash.

Key Requirements

Create a primary logo for “Brel” and a core label for the 2 oz pomade jar (screw-top).

Use a clean, modern style — masculine, confident, and approachable (think Dorran’s, Velta, Northfield Kit).

Design for 1–2 color screen printing on solid jar colors (white, black, or navy).

Avoid gradients, foil, or embossing. Must work in black & white.

Provide: vector logo, mockup of the 2 oz jar, color palette (CMYK/RGB/HEX), and font specs.

Winning design may lead to future projects (body wash, shave gel, skincare lines).

Font styles to use
Other font styles liked:
• We like the fonts and design concept in the attached mockup.

Requirements
Should not have
• We want to avoid too much writing or busy designs. We want to avoid having graphics/illustrations embedded in the logo if they will cause the brand to look less classy or sophisticated. We also want the design to look simple and all-American (e.g. Hollister and Vane, Pine Ledger, The KIM, etc). We’d like to give a Pellham & Royce vibe that feels classy and high end.

```html
<!DOCTYPE html>
<html lang="en">
<head>
<meta charset="UTF-8">
<title>Brel Hair Pomade Label</title>
<link rel="stylesheet" href="https://fonts.googleapis.com/css2?family=Playfair+Display:wght@600&display=swap">
<style>
  :root {
    --ink: #0b0b0b;
    --paper: #ffffff;
    --backdrop: #e4e5e8;
  }
  html, body {
    margin: 0;
    padding: 0;
    width: 1200px;
    height: 800px;
    overflow: hidden;
    background: var(--backdrop);
  }
  .canvas {
    width: 1200px;
    height: 800px;
    display: flex;
    align-items: center;
    justify-content: center;
  }
  .label {
    position: relative;
    width: 800px;
    height: 420px;
    box-sizing: border-box;
    padding-top: 60px;
    background: var(--paper);
    border-radius: 6px;
    display: flex;
    flex-direction: column;
    align-items: center;
    font-family: "Playfair Display", Georgia, serif;
    font-weight: 600;
    color: var(--ink);
  }
  .brand-name {
    margin: 0;
    font-size: 130px;
    font-weight: 600;
    line-height: 1;
  }
  .tagline {
    margin: 18px 0 0;
    font-size: 20px;
    line-height: 1.2;
  }
  .product-type {
    margin: 26px 0 0;
    padding: 3px 12px 5px;
    background: var(--ink);
    color: var(--paper);
    border-radius: 7px;
    font-size: 24px;
    line-height: 1.2;
  }
  .spec {
    position: absolute;
    bottom: 30px;
    margin: 0;
    font-size: 13px;
    line-height: 1.2;
    letter-spacing: 0.2px;
  }
  .spec--hold { left: 110px; }
  .spec--weight { right: 110px; }
</style>
</head>
<body>
  <main class="canvas">
    <section class="label">
      <h1 class="brand-name">Brel</h1>
      <p class="tagline">Fresh &amp; Clean</p>
      <p class="product-type">Hair Pomade</p>
      <p class="spec spec--hold">Medium Hold - Matte Finish</p>
      <p class="spec spec--weight">Net WT 2 oz (57g)</p>
    </section>
  </main>
</body>
</html>
```